Online interactive calendar for training organisation

We have a new website being made and need a design for an online calendar that is interactive and very simple and easy to use. On our main page this calendar will include all of our courses (approx 30 different ones with up to 8 different locations). On our sub pages which have course information, the calendar will only include details of that specific course. Details needed are: Course code, course name/title, date, duration (1/2 day - 5 days), location, price, discount price. Maybe also a key for available or limited spots left? We want a section at the top of the calendar to be able to filter by location or course, and maybe to filter by month also? I have included a spreadsheet with a sample of our courses with this information. Also a sample draft of the main page on our new webpage to show the colour green which is our company colour. Main notes - we want as simple, effective and easy to use as possible.
We will need to know what plug in we can use to get the design you have created.

Target Market(s)

Mining and construction - both companies and individuals

Number of Pages Required

1 page

Colors
cadf82

Requirements
Must have
• Be simple, easy to use, effective.

```html
<!DOCTYPE html>
<html lang="en">
<head>
<meta charset="utf-8">
<title>Course Calendar</title>
<link rel="stylesheet" href="https://fonts.googleapis.com/css2?family=Lato:wght@400;700;900&display=swap">
<style>
:root{
  --page:#f0f0f0;
  --ink:#1e1e1e;
  --muted:#4a4a4a;
  --brand-green:#cadf82;
  --loc-green:#6b8a1e;
  --brand-red:#d9141b;
  --line:#e3e3e3;
  --panel:#e6e5e5;
  --panel-edge:#dcdcdc;
  --white:#ffffff;
}
*{box-sizing:border-box;margin:0;padding:0}
html,body{width:1200px;height:1095px;overflow:hidden}
body{background:var(--page);font-family:'Lato',sans-serif;color:var(--ink);position:relative}
.brand{position:absolute;left:0;width:1200px;top:44px;display:flex;justify-content:center;align-items:center;gap:14px}
.brand-mark{width:46px;height:46px;border-radius:50%;background:var(--brand-red)}
.brand-text{display:flex;flex-direction:column;align-items:center}
.brand-name{font-weight:900;font-size:30px;color:var(--brand-red);letter-spacing:1px;line-height:1}
.brand-tag{font-size:13px;margin-top:9px;letter-spacing:.3px}
.page-title{position:absolute;top:176px;width:1200px;text-align:center;font-weight:400;font-size:31px}
.intro{position:absolute;top:232px;width:1200px;text-align:center;font-size:12.6px;line-height:22px;color:var(--muted)}
.filters{position:absolute;left:112px;top:304px;width:978px;height:92px;background:var(--panel);border:2px solid var(--panel-edge);border-radius:3px}
.filter{position:absolute;top:22px;height:50px;background:var(--white);border:1px solid #d4d4d4;border-radius:2px;display:flex;align-items:center;padding:0 12px;font-size:21px;color:#555}
.filter svg.icon{width:16px;height:18px;margin-right:6px;fill:#555}
.filter .caret{position:absolute;right:14px;top:22px;border-left:4px solid transparent;border-right:4px solid transparent;border-top:5px solid #333}
.f-location{left:24px;width:303px}
.f-course{left:344px;width:303px}
.f-month{left:660px;width:303px}
.options{position:absolute;left:290px;top:367px;width:129px;height:40px;background:var(--white);box-shadow:0 1px 3px rgba(0,0,0,.2);font-size:13px;padding:13px 13px}
.options::before{content:"";position:absolute;right:10px;top:-7px;border-left:7px solid transparent;border-right:7px solid transparent;border-bottom:7px solid var(--white)}
.schedule{position:absolute;left:112px;top:431px;width:976px;height:443px;background:var(--brand-green);padding:0 12px 13px 12px;box-shadow:0 1px 3px rgba(0,0,0,.12)}
table{border-collapse:collapse;width:952px;table-layout:fixed}
th{height:59px;color:var(--white);font-weight:400;font-size:15px;text-align:left;padding:0 8px;position:relative;border-left:1px solid #e2edbd;line-height:17px}
th:first-child{border-left:none;padding-left:12px}
th .sort{position:absolute;right:9px;top:27px;border-left:4px solid transparent;border-right:4px solid transparent;border-top:5px solid var(--white)}
td{background:var(--white);border-left:1px solid var(--line);border-top:1px solid var(--line);font-size:13.2px;text-align:center;padding:0 8px;line-height:20.5px}
td:first-child{border-left:none;text-align:left;padding-left:24px}
td.date{text-align:left;padding-left:10px}
td.loc{color:var(--loc-green);font-size:16.5px}
tbody tr{height:69px}
tbody tr:first-child td{border-top:none}
tbody tr:last-child{height:90px}
.limited{color:var(--brand-red);font-size:11px;vertical-align:top}
.key{position:absolute;top:896px;width:1200px;text-align:center;font-size:15px;color:var(--muted)}
.key .star{color:var(--brand-red);font-size:22px;position:relative;top:-10px;margin-right:3px}
.footer{position:absolute;left:0;top:1016px;width:1200px;height:79px;background:var(--white);text-align:center;font-size:15px;color:#333;padding-top:32px}
</style>
</head>
<body>
<header class="brand">
  <span class="brand-mark"></span>
  <div class="brand-text">
    <span class="brand-name">RIDGELINE SAFETY</span>
    <span class="brand-tag">SAFETY AND TRAINING</span>
  </div>
</header>

<h1 class="page-title">CALENDAR</h1>
<p class="intro">Lorem ipsum dolor sit amet, consectetur adipiscing elit, sed do eiusmod tempor incididunt<br>ut labore et dolore magna aliqt enim ad minim veniam, quisorem ipsum dolo</p>

<section class="filters">
  <div class="filter f-location">
    <svg class="icon" viewBox="0 0 16 18"><path d="M8 0a6 6 0 0 0-6 6c0 4.5 6 12 6 12s6-7.5 6-12a6 6 0 0 0-6-6zm0 8.5A2.5 2.5 0 1 1 8 3.5a2.5 2.5 0 0 1 0 5z"/></svg>Location<span class="caret"></span>
  </div>
  <div class="filter f-course">
    <svg class="icon" viewBox="0 0 16 18"><path d="M4 2h11l-3 13H1zM5.5 5h7l-.3 1.4h-7zm-.6 3h7l-.3 1.4h-7z" fill-rule="evenodd"/></svg>Course<span class="caret"></span>
  </div>
  <div class="filter f-month">
    <svg class="icon" viewBox="0 0 16 18"><path d="M1 4h14v13H1zM2.5 8v7.5h11V8zM4 1h2v4H4zm6 0h2v4h-2z" fill-rule="evenodd"/></svg>Month<span class="caret"></span>
  </div>
</section>
<div class="options">Yatala</div>

<section class="schedule">
  <table>
    <colgroup><col style="width:227px"><col style="width:189px"><col style="width:94px"><col style="width:126px"><col style="width:103px"><col style="width:86px"><col style="width:127px"></colgroup>
    <thead>
      <tr>
        <th>Course code &amp; title<span class="sort"></span></th>
        <th>Course time<span class="sort"></span></th>
        <th>Time<span class="sort"></span></th>
        <th>Duration<span class="sort"></span></th>
        <th>Location<span class="sort"></span></th>
        <th>Price<span class="sort"></span></th>
        <th>BTF<br>discount price<span class="sort"></span></th>
      </tr>
    </thead>
    <tbody>
      <tr><td>RIIHAN304D Work safely<br>at heights</td><td class="date">Tuesday, october, 29 , 2019</td><td>8 am</td><td>1 day</td><td class="loc">Yatala</td><td>$500</td><td>$120</td></tr>
      <tr><td>RIIHAN304D Work safely<br>at heights <span class="limited">*</span></td><td class="date">Tuesday, October, 29 , 2019</td><td>8 am</td><td>1 day</td><td class="loc">Yatala</td><td>$500</td><td>$120</td></tr>
      <tr><td>HLTAID005 Confined space -<br>practical only (theory online)</td><td class="date">Thursday, January, 30 , 2019</td><td>1pm</td><td>1/2 day</td><td class="loc">Yatala</td><td>$80</td><td></td></tr>
      <tr><td>HLTAID001 First Aid -<br>practical only</td><td class="date">Friday, November, 15 , 2019</td><td>1pm</td><td>1/2 day</td><td class="loc">Yatala</td><td>$80</td><td></td></tr>
      <tr><td>CPCCCM208 Dogging &amp;<br>TLILIC0005 front end loader<br>BUNDLE</td><td class="date">Monday, October, 28 , 2019</td><td>8 am</td><td>10 days</td><td class="loc">Yatala</td><td>$2300</td><td>$1200</td></tr>
    </tbody>
  </table>
</section>

<p class="key"><span class="star">*</span>Limited spots left</p>

<footer class="footer">© 2019 All Rights Reserved. Site map. Terms and Conditions</footer>
</body>
</html>
```